Creation of an elegant and modern turnkey Shopify website

Hello,

We are a new company specializing in the sale of above-ground pools. We want to create a turnkey website, ideally using Shopify. For now, we need a "showcase" site, not an e-commerce platform, with four tabs:

Home Page (an overall presentation of the company)
Our Products (an overview of all the above-ground pools we sell)
Our Projects (a page inspired by Photogram to showcase photos of our future projects)
Contact (a page with all our contact information and a contact form)

We are looking to create a highly visual, elegant, and modern website with vibrant splashes of color. We will provide the text, photos (along with instructions on where to place them on each page), and all other necessary information as attachments.

Thank you in advance for your proposals!

The Brisa Lagoon Team

Target Market(s)

Targeted at Swiss customers (a translator will need to be installed for different languages)

Industry/Entity Type

Sale of customised above-ground pools

Coding

Coded - Design and coding required

Font styles to use
Sans Serif

Colors
0094D4
00A9DD
6FCCEA
C7EBF8
E9F6FB
00AB8E
00BBA5
67D7C9
C6EFE9
E9F9F6

Requirements
Must have
• A stunning, elegant and modern look
Nice to have
• Inspiration from the colors of our logo throughout the site, but in an elegant way
Should not have
• An overly classic look for swimming pool sites

```html
<!DOCTYPE html>
<html lang="en">
<head>
<meta charset="utf-8">
<title>Brisa Lagoon – Premium Above-Ground Pools</title>
<link href="https://fonts.googleapis.com/css2?family=DM+Sans:wght@400;500;700&family=Open+Sans:wght@400;600&display=swap" rel="stylesheet">
<style>
:root{
  --blue-deep:#0094D4;
  --sky-pale:#C7EBF8;
  --sky-mist:#E9F6FB;
  --sky-light:#C4E8F6;
  --green:#00AB8E;
  --teal:#3DAA98;
  --teal-dark:#0E8A76;
  --mint-mist:#F2FBFB;
  --foot:#9ADDE5;
  --ink:#1F2D3A;
  --grey:#7A8288;
  --white:#ffffff;
  --sea-dark:#1C6E63;
}
*{box-sizing:border-box;margin:0;padding:0}
html,body{width:1200px;height:4566px;overflow:hidden}
body{position:relative;background:var(--white);font-family:"Open Sans",sans-serif;color:var(--ink)}
.abs{position:absolute}
.photo{position:absolute}
h1,h2,h3,.display{font-family:"DM Sans",sans-serif;font-weight:500}

/* nav */
.topbar{left:0;top:0;width:1200px;height:97px;background:var(--mint-mist)}
.brand{left:92px;top:20px;width:60px;font-family:"DM Sans",sans-serif;font-size:17px;line-height:22px;color:var(--green);letter-spacing:1px;text-align:center}
.menu{right:100px;top:28px;display:flex;gap:40px;font-size:15px;font-family:"DM Sans",sans-serif;color:#3a4650}
.menu .active{color:var(--green)}

/* hero */
.hero-panel{left:0;top:97px;width:475px;height:456px;background:var(--sky-light)}
.hero-title{left:83px;top:145px;width:360px;font-size:39px;line-height:61px;font-weight:700;color:#8A8F93}
.hero-title .hl{color:var(--teal-dark)}
.hero-lede{left:83px;top:393px;width:340px;font-size:14px;line-height:25px;color:#4d5a63}
.btn-solid{display:flex;align-items:center;justify-content:center;background:var(--teal-dark);color:#fff;font-family:"DM Sans",sans-serif;font-weight:700;font-size:12px}
.hero-btn{left:83px;top:462px;width:131px;height:42px}
.hero-photo{left:491px;top:97px;width:709px;height:456px;background:linear-gradient(135deg,#BFE8E8,#8FD4D6 50%,#B9E5E3)}

/* about */
.about-panel{left:0;top:569px;width:679px;height:384px;background:var(--teal)}
.about-kicker{left:85px;top:605px;color:#fff;font-size:18px;font-family:"DM Sans",sans-serif}
.about-title{left:85px;top:632px;color:#fff;font-size:34px}
.about-copy{left:85px;top:688px;width:540px;color:#EAF8F5;font-size:12.2px;line-height:24.8px}
.about-copy u{color:#fff}
.btn-ghost{display:flex;align-items:center;justify-content:center;gap:8px;border:1.5px solid rgba(255,255,255,.7);border-radius:20px;color:#fff;font-size:13px}
.about-btn{left:85px;top:885px;width:134px;height:40px}
.about-photo{left:702px;top:569px;width:498px;height:384px;background:linear-gradient(180deg,#9FC8E8,#DDE6EC 55%,#5CB8D6)}

/* why */
.why{left:0;top:969px;width:1200px;height:649px;background:var(--sky-light)}
.center{text-align:center}
.why-kicker{left:0;top:1010px;width:1200px;font-size:15px;color:#3a4650}
.why-title{left:0;top:1040px;width:1200px;font-size:34px;color:#1c2733}
.why-lede{left:290px;top:1100px;width:620px;font-size:12px;line-height:19px;color:var(--grey)}
.feature{position:absolute;width:309px;height:159px;background:#fff;text-align:center;padding:48px 30px 0}
.feature h3{font-family:"Open Sans",sans-serif;font-weight:600;font-size:13px;color:#2F6E93;margin-bottom:18px}
.feature p{font-size:11.5px;line-height:17px;color:#5b6670}
.badge{position:absolute;left:50%;top:-21px;margin-left:-21px;width:42px;height:42px;border-radius:50%;background:var(--green);border:3px solid #fff;color:#fff;font-family:"DM Sans",sans-serif;font-size:24px;display:flex;align-items:center;justify-content:center}

/* products */
.products{left:0;top:1634px;width:1200px;height:469px;background:var(--sky-mist)}
.product{position:absolute;top:1634px;width:392px;height:469px;background:var(--sky-light)}
.product .pic{height:292px}
.product h3{text-align:center;font-size:27px;color:#3a4650;margin-top:16px}
.meta{display:flex;justify-content:center;gap:14px;margin-top:10px;font-size:13px;color:#5a9bb0}
.meta span{display:flex;align-items:center;gap:5px}
.product .btn-solid{margin:16px 15px 0;height:50px;font-size:15px;background:var(--green)}

/* services */
.service{position:absolute;top:2119px;width:592px;height:385px;background:var(--sky-light);padding:74px 85px 0}
.service .kick{font-size:18px;color:#8AA0A8;font-family:"DM Sans",sans-serif}
.service h2{font-size:34px;color:var(--teal);margin:4px 0 18px}
.service p{font-size:12.3px;line-height:24.8px;color:#4d5a63}
.service .btn-ghost{border-color:var(--teal);color:var(--teal);border-radius:0;width:136px;height:44px;margin-top:28px}
.service.right{text-align:right}
.service.right .btn-ghost{margin-left:auto}

/* gallery */
.gallery-head{left:0;top:2520px;width:1200px;height:179px;background:var(--teal);color:#fff}
.gallery-head .kick{margin-top:32px;font-size:15px}
.gallery-head h2{font-size:34px;margin:12px 0 16px}
.gallery-head p{font-size:12px}
.tile{position:absolute;width:392px;height:385px}
.tile-text{background:var(--mint-mist);text-align:center;padding-top:105px}
.tile-text h3{font-size:34px;line-height:53px;color:#1c2733}
.tile-text p{margin:18px auto 0;width:300px;font-size:12px;line-height:19px;color:var(--grey)}

/* cta */
.cta{left:0;top:3916px;width:1200px;height:276px;background:linear-gradient(135deg,#1E7A6E,var(--sea-dark) 50%,#2A8A7C);color:#fff}
.cta h2{font-weight:700;font-size:34px;line-height:43px;margin-top:40px}
.cta p{font-size:15px;margin-top:24px}
.cta .btn-solid{margin:20px auto 0;width:275px;height:50px;background:var(--green);font-size:15px}

/* footer */
.footer{left:0;top:4208px;width:1200px;height:358px;background:var(--foot)}
.foot-brand{left:95px;top:4248px;width:120px;text-align:center;font-family:"DM Sans",sans-serif;font-size:34px;line-height:40px;color:#1c2733}
.news-label{left:81px;top:4388px;font-size:12px;font-weight:600;color:#3a4650}
.news{left:81px;top:4412px;display:flex}
.news .field{width:217px;height:38px;background:#fff;font-size:12px;color:#3a4650;padding:12px 16px}
.news .btn-solid{width:70px;height:38px;background:var(--green);font-size:13px}
.col{position:absolute;top:4240px;font-size:12.5px}
.col h4{font-family:"DM Sans",sans-serif;font-weight:700;font-size:15px;color:#46545e;margin-bottom:12px}
.col li{list-style:none;color:#5E7F88;line-height:34px}
.rule{left:70px;top:4500px;width:1060px;height:1px;background:#7FC2CB}
.copyright{left:0;top:4535px;width:1200px;font-size:11px;color:#3a4650}
</style>
</head>
<body>

<header class="abs topbar"></header>
<div class="abs brand">BRISA<br>LAGOON</div>
<nav class="abs menu"><span class="active">Home</span><span>Our Product</span><span>Our Project</span><span>Contact Us</span></nav>

<section>
  <div class="abs hero-panel"></div>
  <h1 class="abs hero-title"><span class="hl">Transform</span> Your Garden with Our <span class="hl">Premium</span> Above-<span class="hl">Ground Pools!</span></h1>
  <p class="abs hero-lede">Achieve your dreams with our custom, tailor-made above-ground pools.</p>
  <a class="abs btn-solid hero-btn">Get started</a>
  <div class="photo hero-photo" role="img" aria-label="Aerial view of a person floating on a pink ring in clear turquoise water"></div>
</section>

<section>
  <div class="abs about-panel"></div>
  <div class="abs about-kicker">About Us</div>
  <h2 class="abs about-title">About Brisa Lagoon</h2>
  <p class="abs about-copy">Cedar Hollow Ranch is legendary for it’s Native &amp; Exotic hunting which includes whitetail deer hunting, turkey hunting, and 60+ additional species available for hunt! You will see thousands of wildlife free ranging on over 18,000 acres of the Verdant Hills. A few of the species you will encounter on your visit include giraffes, zebras, kangaroos, axis, bongo, kudu blackbucks, elk, hogs, red stags, and of course record-breaking whitetail deer. Cedar Hollow Ranch is home to <u>ironroll-park.example</u> which is the only place in the world you can drive and shoot real WWII tanks!primarily be a hunting ranch</p>
  <a class="abs btn-ghost about-btn">Read more <svg width="11" height="11" viewBox="0 0 11 11"><path d="M2 9L9 2M4 2h5v5" stroke="currentColor" fill="none" stroke-width="1.2"/></svg></a>
  <div class="photo about-photo" role="img" aria-label="Modern white villa with an outdoor swimming pool"></div>
</section>

<section>
  <div class="abs why"></div>
  <div class="abs why-kicker center">Why Us</div>
  <h2 class="abs why-title center">Acquisition strategy and future plans</h2>
  <p class="abs why-lede center">Borem ipsum dolor sit amet, consectetur adipiscing elit. Etiam eu turpis molestie, dictum est a, mattis tellus. Sed dignissim, metus nec fringilla</p>
  <div class="feature" style="left:99px;top:1198px"><span class="badge">1</span><h3>Superior Quality</h3><p>Each pool is constructed with high-quality materials, ensuring exceptional durability and strength.</p></div>
  <div class="feature" style="left:445px;top:1198px"><span class="badge">2</span><h3>Elegant Design</h3><p>Our pools come in a variety of styles and finishes, seamlessly blending into any garden setting.</p></div>
  <div class="feature" style="left:790px;top:1198px"><span class="badge">3</span><h3>Custom and Tailor-Made</h3><p>Create the pool of your dreams with our customization options, tailored to your specific tastes and needs.</p></div>
  <div class="feature" style="left:275px;top:1418px"><span class="badge">4</span><h3>Easy Installation</h3><p>1. Enjoy your new oasis quickly with our simple and fast installation process.</p></div>
  <div class="feature" style="left:615px;top:1418px"><span class="badge">5</span><h3>Constant Innovation</h3><p>We incorporate the latest technologies to provide you with an optimal and safe swimming experience.</p></div>
</section>

<section>
  <div class="abs products"></div>
  <article class="product" style="left:0">
    <div class="pic" role="img" aria-label="Garden swimming pool surrounded by palm trees and umbrellas" style="background:linear-gradient(180deg,#5FA3D9,#4E8F4A 50%,#2FA6D8)"></div>
    <h3>Garden Swimming Pool</h3>
    <div class="meta"><span><svg width="14" height="10"><rect x="1" y="3" width="12" height="6" fill="none" stroke="currentColor"/><rect x="3" y="1" width="8" height="3" fill="none" stroke="currentColor"/></svg>5 Rooms</span><span><svg width="14" height="10"><rect x="1" y="3" width="12" height="6" fill="none" stroke="currentColor"/><rect x="3" y="1" width="8" height="3" fill="none" stroke="currentColor"/></svg>5 Rooms</span><span><svg width="12" height="12"><circle cx="6" cy="6" r="4.5" fill="none" stroke="currentColor"/></svg>10×8m²</span></div>
    <a class="btn-solid">Detail</a>
  </article>
  <article class="product" style="left:404px">
    <div class="pic" role="img" aria-label="Indoor lap swimming pool under a white ceiling" style="background:linear-gradient(180deg,#D9DCDF,#9CB6C4 40%,#1E98D8)"></div>
    <h3>Indoor swimming Pool</h3>
    <div class="meta"><span><svg width="14" height="10"><rect x="1" y="3" width="12" height="6" fill="none" stroke="currentColor"/><rect x="3" y="1" width="8" height="3" fill="none" stroke="currentColor"/></svg>5 Rooms</span><span><svg width="14" height="10"><rect x="1" y="3" width="12" height="6" fill="none" stroke="currentColor"/><rect x="3" y="1" width="8" height="3" fill="none" stroke="currentColor"/></svg>5 Rooms</span><span><svg width="12" height="12"><circle cx="6" cy="6" r="4.5" fill="none" stroke="currentColor"/></svg>10×8m²</span></div>
    <a class="btn-solid">Detail</a>
  </article>
  <article class="product" style="left:808px">
    <div class="pic" role="img" aria-label="Outdoor pool with a stone pavilion and wooded hills" style="background:linear-gradient(180deg,#8FB7CC,#3F5E3E 45%,#36B3D6)"></div>
    <h3>Basic Adult Swimming Pool</h3>
    <div class="meta"><span><svg width="14" height="10"><rect x="1" y="3" width="12" height="6" fill="none" stroke="currentColor"/><rect x="3" y="1" width="8" height="3" fill="none" stroke="currentColor"/></svg>5 Rooms</span><span><svg width="14" height="10"><rect x="1" y="3" width="12" height="6" fill="none" stroke="currentColor"/><rect x="3" y="1" width="8" height="3" fill="none" stroke="currentColor"/></svg>5 Rooms</span><span><svg width="12" height="12"><circle cx="6" cy="6" r="4.5" fill="none" stroke="currentColor"/></svg>10×8m²</span></div>
    <a class="btn-solid">Detail</a>
  </article>
</section>

<section>
  <div class="service" style="left:0">
    <div class="kick">Our services</div>
    <h2>Personalized Services</h2>
    <p>We understand that every garden and client is unique. That’s why we offer personalized services, from design to installation and after-sales support. Our team of experts is here to answer all your questions and guide you throughout your project.</p>
    <a class="btn-ghost">Read more <svg width="11" height="11" viewBox="0 0 11 11"><path d="M2 9L9 2M4 2h5v5" stroke="currentColor" fill="none" stroke-width="1.2"/></svg></a>
  </div>
  <div class="service right" style="left:608px">
    <div class="kick">Our Services</div>
    <h2>Guaranteed Satisfaction</h2>
    <p>Your satisfaction is our top priority. We are committed to providing you with exceptional service and the highest quality products. Join our community of satisfied customers who are already enjoying their custom above-ground pools. 10-Year Warranty!</p>
    <a class="btn-ghost">Read more <svg width="11" height="11" viewBox="0 0 11 11"><path d="M2 9L9 2M4 2h5v5" stroke="currentColor" fill="none" stroke-width="1.2"/></svg></a>
  </div>
</section>

<section>
  <div class="abs gallery-head center">
    <div class="kick">Our work</div>
    <h2>Brisa Lagoon Project Gallery</h2>
    <p>Borem ipsum dolor sit amet, consectetur adipiscing elit. Etiam eu turpis molestie, dictum est a.</p>
  </div>
  <div class="tile" style="left:0;top:2715px;background:linear-gradient(180deg,#6E93B5,#F1D8B0 35%,#2C8FD0 60%,#2B2E33)" role="img" aria-label="Rooftop pool at dusk"></div>
  <div class="tile" style="left:404px;top:2715px;background:linear-gradient(180deg,#E6D5C3,#C78B59 50%,#2A6F90)" role="img" aria-label="Resort pool with parasols at sunset"></div>
  <div class="tile tile-text" style="left:808px;top:2715px"><h3>Brisa Lagoon<br>Project Gallery 1</h3><p>Borem ipsum dolor sit amet, consectetur adipiscing elit. Etiam eu turpis molestie, dictum</p></div>
  <div class="tile" style="left:0;top:3115px;background:radial-gradient(circle at 55% 45%,#2AA6DB,#2F6B33 45%,#3E7B3A)" role="img" aria-label="Aerial view of a freeform pool among tropical trees"></div>
  <div class="tile tile-text" style="left:404px;top:3115px"><h3>Brisa Lagoon<br>Project Gallery 2</h3><p>Borem ipsum dolor sit amet, consectetur adipiscing elit. Etiam eu turpis molestie, dictum</p></div>
  <div class="tile" style="left:808px;top:3115px;background:linear-gradient(160deg,#7E9A5C,#2BA7C9 55%,#5D8A4E)" role="img" aria-label="Aerial view of a resort lagoon pool with palms"></div>
  <div class="tile tile-text" style="left:0;top:3516px"><h3>Brisa Lagoon<br>Project Gallery 3</h3><p>Borem ipsum dolor sit amet, consectetur adipiscing elit. Etiam eu turpis molestie, dictum</p></div>
  <div class="tile" style="left:404px;top:3516px;background:linear-gradient(180deg,#A8D6E6,#4FA3C8 50%,#1E7FB5)" role="img" aria-label="Indoor pool with tall windows"></div>
  <div class="tile" style="left:808px;top:3516px;background:linear-gradient(180deg,#EDE8E0,#C8BFAE 60%,#3E9FB8)" role="img" aria-label="Bright indoor pool hall with plants"></div>
</section>

<section class="abs cta center" role="img" aria-label="Rippling dark teal water background">
  <h2>Contact Us Today To Discover Our Range Of Customizable<br>Above-Ground Pools And Get A Tailored Quote</h2>
  <p>Qorem Ipsum Dolor Sit Amet, Consectetur Adipiscing Elit. Nunc Vulputate Libero.</p>
  <a class="btn-solid">Contact Us</a>
</section>

<footer>
  <div class="abs footer"></div>
  <div class="abs foot-brand">BRISA<br>LAGOON</div>
  <div class="abs news-label">Get Our Weekly Newsletter (Zero Spam)</div>
  <div class="abs news"><div class="field">Type In Your Email</div><a class="btn-solid">Send</a></div>
  <div class="col" style="left:512px"><h4>Navigation</h4><ul><li>Home</li><li>Features</li><li>Market</li><li>Blog</li><li>Career</li><li>About Us</li></ul></div>
  <div class="col" style="left:683px"><h4>Features</h4><ul><li>Crypto Wallet</li><li>Exchange Services</li><li>Investment Portfolio</li><li>Portfolio Management</li></ul></div>
  <div class="col" style="left:857px"><h4>Legal</h4><ul><li>Term Of Services</li><li>Privacy Policy</li><li>Licensed &amp; Regulation</li></ul></div>
  <div class="col" style="left:1040px"><h4>Socials</h4><ul><li>ProLink</li><li>Chirp</li><li>FriendHub</li><li>Photogram</li></ul></div>
  <div class="abs rule"></div>
  <div class="abs copyright center">© 2024 Brisa Lagoon All Rights Reserved.</div>
</footer>

</body>
</html>
```